Easy Marinade Labels for Butchery Store

Need a set of labels designed for a Butchery Shop. They will sit in the top left corner of the packets as a triangle (7cm each side). Easy because the only major requirement is the label name and some small text saying "Please ask in store to see spec sheet for ingredients". Extra points for finding a fun way to incorporate the logo and/or images of food (garlic bulbs, chilli, spices ect) to enhance the label. List of Marinade Names below: GarlicPepper Mint & RosemarySatayBBQChilli Plum & GingerSundried Tomato & BasilBuffaloHoney SoyHoi-SinPer PeriSpicy CajunTeriyakiBlack Bean Ive also attached the logo and an example of how the label might sit on a packet of meat. Thanks

Target Market(s)

Butchery Deli Shop Customers

Industry/Entity Type

Food Store

Font styles to use
Serif
Sans Serif
Decorative
Other font styles liked:
• Fun font that isn't a generic Quellbrix Font?

Colors

Designer to choose colors to be used in the design.

Requirements
Must have
• Product Name
• Small text saying "Please ask in store to see spec sheet for ingredients"
Nice to have
• Photos of ingredients that would match that type of marinade - Chilli, Garlic, Spices.
• Fenly Oak Logo - not essential if it doesn't look good on the label / doesn't fit.

```html
<!DOCTYPE html>
<html lang="en">
<head>
<meta charset="UTF-8">
<title>Marinade Label – Cajun</title>
<link href="https://fonts.googleapis.com/css2?family=Montserrat:wght@800&family=Oswald:wght@700&family=Permanent+Marker&display=swap" rel="stylesheet">
<style>
  :root {
    --page: #ffffff;
    --frame: #f2e71c;
    --spice-red: #a8321a;
    --spice-deep: #6e1e10;
    --spice-orange: #e8861e;
    --herb-green: #4f8a35;
    --herb-dark: #2c5a22;
    --garlic: #c9c6a0;
    --ink: #ffffff;
    --shadow: #1a1a1a;
  }
  html, body {
    margin: 0;
    padding: 0;
    width: 1200px;
    height: 900px;
    overflow: hidden;
    background: var(--page);
  }
  .label {
    position: relative;
    width: 1200px;
    height: 900px;
  }
  .label__shape {
    position: absolute;
    inset: 0;
  }
  .label__text {
    position: absolute;
    left: 0;
    width: 1200px;
    text-align: center;
    color: var(--ink);
    margin: 0;
  }
  .label__intro {
    top: 376px;
    left: 2px;
    font-family: "Montserrat", sans-serif;
    font-weight: 800;
    font-size: 14px;
    letter-spacing: 2.6px;
    text-shadow: 1px 1px 0 var(--shadow);
  }
  .label__name {
    top: 398px;
    left: 4px;
    font-family: "Permanent Marker", cursive;
    font-size: 112px;
    line-height: 1;
    letter-spacing: 4px;
    text-shadow: 3px 3px 0 var(--shadow);
  }
  .label__note {
    top: 594px;
    left: -2px;
    font-family: "Oswald", sans-serif;
    font-weight: 700;
    font-size: 22px;
    letter-spacing: 2.4px;
    text-shadow: 2px 2px 0 var(--shadow);
  }
</style>
</head>
<body>
<main class="label">
  <svg class="label__shape" width="1200" height="900" viewBox="0 0 1200 900" xmlns="http://www.w3.org/2000/svg">
    <defs>
      <linearGradient id="spice-base" x1="0" y1="0" x2="1" y2="0">
        <stop offset="0" stop-color="var(--garlic)"/>
        <stop offset="0.18" stop-color="var(--spice-red)"/>
        <stop offset="0.45" stop-color="var(--spice-deep)"/>
        <stop offset="0.7" stop-color="var(--spice-red)"/>
        <stop offset="1" stop-color="var(--herb-dark)"/>
      </linearGradient>
      <radialGradient id="spice-glow" cx="0.7" cy="0.35" r="0.45">
        <stop offset="0" stop-color="var(--spice-orange)" stop-opacity="0.95"/>
        <stop offset="1" stop-color="var(--spice-orange)" stop-opacity="0"/>
      </radialGradient>
      <radialGradient id="herb-glow" cx="0.52" cy="0.2" r="0.3">
        <stop offset="0" stop-color="var(--herb-green)" stop-opacity="0.9"/>
        <stop offset="1" stop-color="var(--herb-green)" stop-opacity="0"/>
      </radialGradient>
      <clipPath id="triangle-clip">
        <polygon points="621,178 150,643 1091,643"/>
      </clipPath>
    </defs>
    <g class="label__photo" role="img" aria-label="Photo of cajun spice powder with fresh thyme, mint and rosemary sprigs and garlic" clip-path="url(#triangle-clip)">
      <rect x="140" y="170" width="960" height="480" fill="url(#spice-base)"/>
      <rect x="140" y="170" width="960" height="480" fill="url(#spice-glow)"/>
      <rect x="140" y="170" width="960" height="480" fill="url(#herb-glow)"/>
    </g>
    <polygon class="label__frame" points="621,174 146,645 1096,645" fill="none" stroke="var(--frame)" stroke-width="6" stroke-linejoin="miter"/>
  </svg>
  <p class="label__text label__intro">MARINATED WITH</p>
  <h1 class="label__text label__name">CAJUN</h1>
  <p class="label__text label__note">PLEASE ASK IN STORE TO SEE SPEC SHEET FOR INGREDIENTS</p>
</main>
</body>
</html>
```